Online media outlet needs a blog and logo

A new online blog platform is being established in the UK. The blog will be very similar in layout to www.quorvel.co. It will need to have a main story slider showing three slides and block tiles beneath the slider for additional tiles.

The blog platform will be called 'Tandrel Brisk' and will also need a professional looking logo design for the name.

The website should be designed in Word Press.

Industry/Entity Type

Media

Logo Text

Tandrel Brisk

Coding

Coded - Design and coding required

Number of Pages Required

3 page

Font styles to use
Other font styles liked:
• Helvetica

Requirements
Must have
• A slider showing three slides. Be similar to Quor V (see previous comment). Be Word Press compatible.

```html
<!DOCTYPE html>
<html lang="en">
<head>
<meta charset="utf-8">
<title>Tandrel in the UK</title>
<link rel="stylesheet" href="https://fonts.googleapis.com/css2?family=Open+Sans:wght@300;400;600;700&display=swap">
<style>
:root{
  --bar:#1e2125;
  --ink:#333638;
  --muted:#8a8d90;
  --accent:#29a8de;
  --page:#ffffff;
  --soft:#f2f2f2;
  --foot:#2b2c2e;
  --line:#e3e3e3;
}
*{box-sizing:border-box;margin:0;padding:0}
html,body{width:1200px;height:3072px;overflow:hidden}
body{font-family:"Open Sans",Helvetica,Arial,sans-serif;color:var(--ink);background:var(--page);position:relative}

.site-header{position:absolute;top:0;left:0;width:1200px;height:76px;background:var(--bar);display:flex;align-items:center;padding:0 98px;color:#fff}
.brand{font-size:23px;font-weight:300;letter-spacing:.5px;color:#fff}
.main-nav{margin-left:auto;display:flex;gap:30px;font-size:12px;text-transform:uppercase}
.header-social{display:flex;gap:7px;margin-left:28px}
.header-social span{width:24px;height:24px;border:2px solid #fff;border-radius:50%}

.hero{position:absolute;top:76px;left:0;width:1200px;height:522px;
  background:
    radial-gradient(circle at 24% 30%,rgba(40,170,180,.55) 0,rgba(40,170,180,0) 12%),
    radial-gradient(circle at 86% 22%,rgba(40,170,180,.5) 0,rgba(40,170,180,0) 10%),
    radial-gradient(circle at 40% 90%,rgba(230,180,40,.55) 0,rgba(230,180,40,0) 22%),
    radial-gradient(circle at 90% 78%,rgba(200,60,60,.45) 0,rgba(200,60,60,0) 10%),
    linear-gradient(160deg,#8a7a66 0%,#6b5e50 50%,#4a4038 100%)}
.hero-tag{position:absolute;top:188px;left:389px;width:422px;height:54px;border:2px solid #e8eef2;background:rgba(60,130,160,.6);color:#fff;font-size:34px;font-weight:300;text-align:center;line-height:50px}
.hero-title{position:absolute;top:254px;left:0;width:1200px;text-align:center;color:#fff;font-size:42px;font-weight:400}
.slider-dots{position:absolute;top:481px;left:0;width:1200px;display:flex;justify-content:center;gap:12px}
.slider-dots span{width:7px;height:7px;border-radius:50%;background:rgba(255,255,255,.5)}
.slider-dots span.on{background:#fff}

.tile{position:absolute;overflow:hidden;color:#fff}
.tile::after{content:"";position:absolute;left:0;right:0;bottom:0;height:45%;background:linear-gradient(rgba(0,0,0,0),rgba(0,0,0,.55))}
.tile-caption{position:absolute;z-index:1;left:19px;right:70px;bottom:14px;font-size:14px;line-height:18px}
.tile-caption small{display:block;font-size:10px;margin-top:3px}
.tile-share{position:absolute;z-index:1;right:18px;bottom:18px;display:flex;gap:12px}
.tile-share span{width:6px;height:10px;border-radius:1px;background:#fff}
.tile-lg .tile-caption{font-size:19px;line-height:26px;left:36px;right:150px;bottom:24px}
.tile-lg .tile-caption small{font-size:13px;margin-top:4px}

.newsletter{position:absolute;top:1458px;left:0;width:1200px;height:375px;
  background:
    radial-gradient(ellipse at 12% 50%,rgba(120,110,100,.35),rgba(0,0,0,0) 35%),
    radial-gradient(ellipse at 88% 50%,rgba(120,110,100,.35),rgba(0,0,0,0) 35%),
    linear-gradient(90deg,#2c3542,#1e2632 50%,#2c3542);color:#fff;text-align:center}
.newsletter h2{margin-top:62px;font-size:24px;font-weight:600;letter-spacing:1px}
.newsletter p{width:640px;margin:12px auto 0;font-size:15px;line-height:24px;color:#e6e8ea}
.nl-fields{position:absolute;top:197px;left:254px;display:flex;gap:14px}
.nl-fields span{width:338px;height:38px;background:rgba(255,255,255,.22);font-size:12px;line-height:38px;text-align:left;padding-left:16px;color:#ddd}
.nl-button{position:absolute;top:264px;left:492px;width:182px;height:44px;background:var(--accent);font-size:15px;line-height:44px}

.posts{position:absolute;top:1833px;left:0;width:1200px;height:952px;background:var(--soft)}
.card{position:absolute;background:#fff;border:1px solid var(--line);box-shadow:0 1px 3px rgba(0,0,0,.08)}
.card-media{height:205px}
.card-body{padding:18px 22px 0}
.card-cat{font-size:12px;color:var(--accent);text-transform:uppercase}
.card-title{font-size:16px;font-weight:400;margin-top:6px;text-transform:uppercase}
.card-text{font-size:11.5px;line-height:20px;color:var(--muted);margin-top:10px;text-align:justify;hyphens:auto}
.card-foot{display:flex;align-items:center;margin-top:12px}
.card-foot .dot{width:20px;height:20px;border-radius:50%;border:1.5px solid #3b5b9a;margin-right:4px}
.card-foot .dot:nth-child(2){border-color:#29a8de}
.card-foot .dot:nth-child(3){border-color:#c8232c}
.card-foot .dot:nth-child(4){border-color:#d3493a}
.card-foot .dot:nth-child(5){border-color:#b0573a}
.card-foot .acts{margin-left:auto;display:flex;gap:22px}
.card-foot .acts span{width:12px;height:10px;border:1.5px solid #c9c9c9;border-radius:3px}

.site-footer{position:absolute;top:2785px;left:0;width:1200px;height:287px;background:var(--foot);border-top:5px solid var(--accent);color:#fff;text-align:center}
.foot-social{display:flex;justify-content:center;gap:16px;margin-top:58px}
.foot-social span{width:54px;height:54px;border:3px solid #fff;border-radius:50%}
.foot-nav{margin-top:28px;font-size:11px;display:flex;justify-content:center;gap:22px}
.foot-nav i{font-style:normal;color:#888}
.copy{margin-top:40px;font-size:12px;color:#6d6f72}
</style>
</head>
<body>
<header class="site-header">
  <div class="brand">TANDREL IN THE UK</div>
  <nav class="main-nav"><span>Home</span><span>Current Topics</span><span>Tandrel Weekend</span><span>Government</span><span>Politics</span><span>Contact Us</span></nav>
  <div class="header-social"><span></span><span></span><span></span></div>
</header>

<section class="hero" role="img" aria-label="Photo of hands using tablets and phones over a table with round media badges">
  <div class="hero-tag">TANDREL IN THE UK.</div>
  <h1 class="hero-title">WE ARE AN ONLINE MEDIA</h1>
  <div class="slider-dots"><span></span><span class="on"></span><span></span></div>
</section>

<section class="tiles">
  <article class="tile" style="left:98px;top:639px;width:320px;height:244px;background:radial-gradient(circle at 55% 40%,#3a9fc8 0,rgba(58,159,200,0) 30%),linear-gradient(160deg,#c9d8e4,#6c8aa4 55%,#2c4258)" role="img" aria-label="Photo of a hand holding a smartphone">
    <p class="tile-caption">There are variations of passages of Lorem Ipsum ?<small>Reviews on May 02</small></p><div class="tile-share"><span></span><span></span></div>
  </article>
  <article class="tile" style="left:440px;top:639px;width:320px;height:244px;background:radial-gradient(circle at 30% 60%,#c0455a 0,rgba(192,69,90,0) 28%),radial-gradient(circle at 70% 55%,#4a4ab0 0,rgba(74,74,176,0) 30%),linear-gradient(160deg,#9a9a9a,#6a6070)" role="img" aria-label="Illustration of colourful media icons around a cloud">
    <p class="tile-caption">There are variations of passages of Lorem Ipsum ?<small>Reviews on May 02</small></p><div class="tile-share"><span></span><span></span></div>
  </article>
  <article class="tile" style="left:782px;top:639px;width:320px;height:244px;background:radial-gradient(ellipse at 50% 70%,#e0a020 0,rgba(224,160,32,0) 25%),radial-gradient(circle at 50% 55%,#2f6fb0,#141826 70%)" role="img" aria-label="Illustration of app icons arching over a tablet">
    <p class="tile-caption">There are variations of passages of Lorem Ipsum ?<small>Reviews on May 02</small></p><div class="tile-share"><span></span><span></span></div>
  </article>
  <article class="tile" style="left:98px;top:905px;width:320px;height:244px;background:linear-gradient(160deg,#d8d4cc,#a8a29a 50%,#5b5650)" role="img" aria-label="Photo of a laptop, coffee cup and phone on a desk">
    <p class="tile-caption">There are variations of passages of Lorem Ipsum ?<small>Reviews on May 02</small></p><div class="tile-share"><span></span><span></span></div>
  </article>
  <article class="tile" style="left:98px;top:1171px;width:320px;height:244px;background:radial-gradient(circle at 55% 35%,#c8d6e0,#5a6470 45%,#22262c 80%)" role="img" aria-label="Photo of glowing icons rising from a phone">
    <p class="tile-caption">There are variations of passages of Lorem Ipsum ?<small>Reviews on May 02</small></p><div class="tile-share"><span></span><span></span></div>
  </article>
  <article class="tile tile-lg" style="left:440px;top:905px;width:662px;height:510px;background:radial-gradient(circle at 78% 18%,#fff4e0 0,rgba(255,244,224,0) 30%),linear-gradient(175deg,#c9c6c2 0%,#9a9a98 35%,#6a5a48 65%,#3b2a1c 100%)" role="img" aria-label="Photo of a person holding a phone over a laptop with a city skyline">
    <p class="tile-caption">There are many variations of passages of Lorem Ipsum available, but the majority have suffered ?<small>Reviews on May 02</small></p><div class="tile-share" style="bottom:26px;right:36px"><span></span><span></span></div>
  </article>
</section>

<section class="newsletter" role="img" aria-label="Photo of young people using phones, darkened">
  <h2>TANDREL &nbsp;NEWSLETTER</h2>
  <p>It is a long established fact that a reader will be distracted by the readable content of a page when looking at its layout. The point of using Lorem Ipsum</p>
  <div class="nl-fields"><span>Enter Your mail id</span><span>Enter Your Phone Number</span></div>
  <div class="nl-button">SUBSCRIBE NOW</div>
</section>

<section class="posts">
  <article class="card" style="left:98px;top:40px;width:320px;height:426px">
    <div class="card-media" role="img" aria-label="Illustration of hanging social media icons" style="background:radial-gradient(circle at 30% 45%,rgba(200,40,60,.35) 0,rgba(200,40,60,0) 14%),radial-gradient(circle at 65% 35%,rgba(30,110,190,.4) 0,rgba(30,110,190,0) 16%),radial-gradient(circle at 50% 75%,rgba(230,150,40,.35) 0,rgba(230,150,40,0) 14%),linear-gradient(#f6f6f6,#e4e8ee)"></div>
    <div class="card-body"><div class="card-cat">Technic</div><h3 class="card-title">Excepteur sint occaecat</h3>
    <p class="card-text">Sed ut perspiciatis unde omnis iste natus error sit voluptatem accusantium doloremque laudantium, totam rem aperiam, eaque ipsa quae ab illo inventore veritatis et quasi</p>
    <div class="card-foot"><span class="dot"></span><span class="dot"></span><span class="dot"></span><span class="dot"></span><span class="dot"></span><div class="acts"><span></span><span></span><span></span></div></div></div>
  </article>
  <article class="card" style="left:440px;top:40px;width:320px;height:426px">
    <div class="card-media" role="img" aria-label="Illustration of colourful icons floating above a person" style="background:radial-gradient(circle at 30% 30%,rgba(240,200,40,.55) 0,rgba(240,200,40,0) 18%),radial-gradient(circle at 20% 55%,rgba(220,60,80,.45) 0,rgba(220,60,80,0) 16%),radial-gradient(circle at 40% 40%,#505050,#262626)"></div>
    <div class="card-body"><div class="card-cat">Gadget</div><h3 class="card-title">Excepteur sint occaecat</h3>
    <p class="card-text">Sed ut perspiciatis unde omnis iste natus error sit voluptatem accusantium doloremque laudantium, totam rem aperiam, eaque ipsa quae ab illo inventore veritatis et quasi</p>
    <div class="card-foot"><span class="dot"></span><span class="dot"></span><span class="dot"></span><span class="dot"></span><span class="dot"></span><div class="acts"><span></span><span></span><span></span></div></div></div>
  </article>
  <article class="card" style="left:782px;top:40px;width:320px;height:426px">
    <div class="card-media" role="img" aria-label="Photo of raised hands holding colourful speech bubbles" style="background:radial-gradient(circle at 25% 45%,rgba(60,170,220,.5) 0,rgba(60,170,220,0) 18%),radial-gradient(circle at 60% 35%,rgba(210,60,60,.5) 0,rgba(210,60,60,0) 16%),radial-gradient(circle at 80% 60%,rgba(180,70,200,.45) 0,rgba(180,70,200,0) 18%),linear-gradient(160deg,#c4c6c8,#8a8a94)"></div>
    <div class="card-body"><div class="card-cat">Gadget</div><h3 class="card-title">Excepteur sint occaecat</h3>
    <p class="card-text">Sed ut perspiciatis unde omnis iste natus error sit voluptatem accusantium doloremque laudantium, totam rem aperiam, eaque ipsa quae ab illo inventore veritatis et quasi</p>
    <div class="card-foot"><span class="dot"></span><span class="dot"></span><span class="dot"></span><span class="dot"></span><span class="dot"></span><div class="acts"><span></span><span></span><span></span></div></div></div>
  </article>
  <article class="card" style="left:98px;top:496px;width:662px;height:412px">
    <div class="card-media" role="img" aria-label="Photo of app icons floating from a phone" style="background:radial-gradient(ellipse at 20% 70%,rgba(40,150,220,.5) 0,rgba(40,150,220,0) 30%),radial-gradient(ellipse at 30% 30%,rgba(220,80,40,.35) 0,rgba(220,80,40,0) 22%),linear-gradient(115deg,#34445e,#8ea0b4 55%,#e2ded8)"></div>
    <div class="card-body"><div class="card-cat">Gadget</div><h3 class="card-title">Excepteur sint occaecat</h3>
    <p class="card-text">Sed ut perspiciatis unde omnis iste natus error sit voluptatem accusantium doloremque laudantium, totam rem aperiam, eaque ipsa quae ab illo inventore veritatis et quasi architecto Sed ut perspiciatis unde omnis iste natus error sit voluptatem accusantium doloremque laudantium</p>
    <div class="card-foot"><span class="dot"></span><span class="dot"></span><span class="dot"></span><span class="dot"></span><span class="dot"></span><div class="acts"><span></span><span></span><span></span></div></div></div>
  </article>
  <article class="card" style="left:782px;top:496px;width:320px;height:412px">
    <div class="card-media" role="img" aria-label="Illustration of a globe made of media icons" style="background:radial-gradient(circle at 50% 50%,#4aa8e8 0,#2d7fc0 25%,#0c1f3a 70%)"></div>
    <div class="card-body"><div class="card-cat">Gadget</div><h3 class="card-title">Excepteur sint occaecat</h3>
    <p class="card-text">Sed ut perspiciatis unde omnis iste natus error sit voluptatem accusantium doloremque laudantium, totam rem aperiam, eaque ipsa quae ab illo inventore veritatis et quasi</p>
    <div class="card-foot"><span class="dot"></span><span class="dot"></span><span class="dot"></span><span class="dot"></span><div class="acts"><span></span><span></span><span></span></div></div></div>
  </article>
</section>

<footer class="site-footer">
  <div class="foot-social"><span></span><span></span><span></span><span></span></div>
  <nav class="foot-nav"><span>HOME</span><i>|</i><span>CURRENT TOPICS</span><i>|</i><span>TANDREL WEEKEND</span><i>|</i><span>GOVERNMENT</span><i>|</i><span>POLITICS</span><i>|</i><span>CONTACT US</span></nav>
  <p class="copy">Copyrights@2016 Brisklane . All rights reserved</p>
</footer>
</body>
</html>
```